Business card for medical clinic

I need an upmarket, modern medical/health business card for my clinic

Contact Information for Business Card

name, address, email, qr code

```html
<!DOCTYPE html>
<html lang="en">
<head>
<meta charset="utf-8">
<title>Corvale Health Partners – Business Card</title>
<link href="https://fonts.googleapis.com/css2?family=Montserrat:wght@400;500;800&display=swap" rel="stylesheet">
<style>
  :root {
    --backdrop: #2b2b2d;
    --card: #ffffff;
    --ink: #1d1d1f;
    --black: #000000;
    --brand-blue: #1f6e9f;
    --accent-deep: #155b8a;
    --accent-light: #2aa3dc;
  }
  * { margin: 0; padding: 0; box-sizing: border-box; }
  html, body {
    width: 1200px; height: 880px; overflow: hidden;
    background: var(--backdrop);
    font-family: "Montserrat", Arial, sans-serif;
  }
  .sheet { position: relative; width: 1200px; height: 880px; }

  .card {
    position: absolute; left: 260px;
    width: 680px; height: 388px;
    background: var(--card);
    border-radius: 26px;
    overflow: hidden;
  }
  .card--front { top: 34px; }
  .card--back  { top: 458px; }

  /* front */
  .front-band { position: absolute; inset: 0; }
  .wordmark {
    position: absolute;
    color: var(--brand-blue);
    font-weight: 500;
    text-transform: uppercase;
    letter-spacing: 0.06em;
    white-space: nowrap;
  }
  .card--front .wordmark { left: 190px; top: 178px; font-size: 24px; }

  /* back */
  .card--back .wordmark { left: 250px; top: 92px; font-size: 20px; }
  .address {
    position: absolute; right: 44px; top: 170px;
    text-align: right; font-size: 15px; line-height: 1.45;
    color: var(--ink); font-style: normal;
  }
  .name-bar {
    position: absolute; left: 0; top: 238px;
    width: 14px; height: 52px;
    background: linear-gradient(180deg, var(--accent-deep), var(--accent-light));
  }
  .person { position: absolute; left: 56px; top: 226px; }
  .person__name {
    font-size: 26px; font-weight: 800; letter-spacing: 0.01em;
    color: var(--brand-blue);
  }
  .person__title { font-size: 16px; color: var(--ink); margin-top: 2px; }
  .divider {
    position: absolute; left: 56px; right: 40px; top: 296px;
    height: 2px; background: var(--accent-deep);
  }
  .contacts {
    position: absolute; left: 56px; top: 310px;
    list-style: none; font-size: 15px; color: var(--ink);
  }
  .contacts li { display: flex; align-items: center; gap: 10px; height: 22px; }
  .contacts svg { width: 14px; height: 14px; flex: none; }
</style>
</head>
<body>
<main class="sheet">

  <section class="card card--front" aria-label="Card front">
    <svg class="front-band" viewBox="0 0 680 388" aria-hidden="true">
      <polygon points="0,0 205,0 205,200 280,200 280,388 0,388" fill="var(--black)"/>
      <circle cx="212" cy="200" r="128" fill="var(--card)"/>
    </svg>
    <div class="wordmark">Corvale Health Partners</div>
  </section>

  <section class="card card--back" aria-label="Card back">
    <div class="wordmark">Corvale Health Partners</div>

    <address class="address">
      Your address, City<br>State, Zip 1234
    </address>

    <div class="name-bar"></div>
    <div class="person">
      <div class="person__name">DANIEL MARSH</div>
      <div class="person__title">Managing Director</div>
    </div>
    <div class="divider"></div>

    <ul class="contacts">
      <li>
        <svg viewBox="0 0 16 16" aria-hidden="true"><path fill="var(--brand-blue)" d="M2 5c0-2 2-3 6-3s6 1 6 3v1h-3V5H5v1H2zM4 7h8l2 6H2z"/></svg>
        123 456 789
      </li>
      <li>
        <svg viewBox="0 0 16 16" aria-hidden="true"><rect x="1" y="3" width="14" height="10" rx="1" fill="var(--brand-blue)"/><path d="M1.5 3.5 8 9l6.5-5.5" stroke="#fff" stroke-width="1.3" fill="none"/></svg>
        hello@corvalehealth.com
      </li>
      <li>
        <svg viewBox="0 0 16 16" aria-hidden="true"><circle cx="8" cy="8" r="7" fill="var(--brand-blue)"/><path d="M1 8h14M8 1c3 3 3 11 0 14M8 1c-3 3-3 11 0 14" stroke="#fff" stroke-width="1" fill="none"/></svg>
        www.corvalehealth.com
      </li>
    </ul>
  </section>

</main>
</body>
</html>
```